Design eines Hausetiketts für traditionelles Weingut
Zielgruppe
Wir das Familienweingut Brandauer in Gimbsheim/Rheinhessen sind ein traditionelles Weingut das seine Reben selbst kultiviert und die Weine auch selbst ausbaut. Wir haben jeden Schritt in der Weinherstellung selbst in der Hand und vermarkten den Wein dann an unsere Privatkunden. Unsere Kundenstruktur sieht folgendermaßen aus: Wir haben 100% Privatkunden die unseren Wein konsumieren. Da jetzt die nächste Generation in den Weinbaubetrieb einsteigt und auch Ideen hat möchten wir ein Hausetikett einführen. Im Moment haben wir noch sehr viele unterschiedliche Etiketten und kein Hausetikett. Da die Verlagsetiketten immer seltener zu unseren Vorstellungen passen, möchten wir hier auf diesem Wege ein Hausetikett anfertigen lassen. Generell möchten wir unseren Außenauftritt komplett modernisieren. Sie können sich über die Vielfalt in unserem Betrieb unter www.weingut-brandauer-beispiel.de einen Überblick verschaffen. Langfristig gesehen wollen wir aber unsere Weinkarte verkleinern.
Aufgabenstellung
Wir haben uns vor ca. 1,5 Jahren hier auf dieser Website bereits ein Logo designen lassen. Es wäre schön wenn man das Logo bei den Entwürfen für die Etiketten berücksichtigen würde. Das wäre aber KEIN MUSS. Auch wäre es gut wenn man das ,,Wein' bei unserem Namen weglassen könnte.
Das Etikett sollte aus Vorder-und Rückenetikett bestehen und edel wirken. Vorne sollte die Rebsorte und die Geschmacksangabe stehen. Der Rest sollte auf das Rückenetikett.
Das Vorderetikett sollte ein richtiger Eyecatcher sein und im Supermarkt z.B. aus vielen anderen herausstechen. Das wäre ganz wichtig.
Man kann bei den Farben unterscheiden in 3 Konzepte.
Literwein als einsteiger Wein
Dann die Gutsweine und zum Schluss die Lagenweine. Alles Farblich oder im design etwas abgesetzt.

```html
<!DOCTYPE html>
<html lang="de">
<head>
<meta charset="utf-8">
<title>Rückenetikett – Familienweingut Brandauer</title>
<link rel="stylesheet" href="https://fonts.googleapis.com/css2?family=Cinzel:wght@400;500&display=swap">
<style>
  :root {
    --label-bg: #faeddf;
    --gold: #a57a4a;
    --berry: #e0162b;
    --legal-text: #c6a892;
    --address-text: #7a4a22;
    --rule-dark: #4a4a4a;
    --rule-gold: #c49a68;
  }
  html, body {
    margin: 0;
    padding: 0;
    overflow: hidden;
    background: var(--label-bg);
  }
  .back-label {
    position: relative;
    width: 1200px;
    height: 792px;
    background: var(--label-bg);
    font-family: "Cinzel", "Times New Roman", serif;
    text-transform: uppercase;
    overflow: hidden;
  }
  .brand {
    position: absolute;
    top: 92px;
    left: 0;
    width: 1200px;
    text-align: center;
  }
  .brand-dot {
    display: block;
    width: 26px;
    height: 26px;
    margin: 0 auto 36px;
    border-radius: 50%;
    background: var(--berry);
  }
  .brand-name {
    margin: 0;
    font-size: 58px;
    font-weight: 400;
    letter-spacing: 1px;
    line-height: 1;
    color: var(--gold);
  }
  .divider {
    position: absolute;
    top: 296px;
    left: 296px;
    width: 590px;
    height: 2px;
    background: linear-gradient(to right, var(--rule-dark) 0%, var(--rule-dark) 75%, var(--rule-gold) 100%);
  }
  .legal-info,
  .winery-address {
    position: absolute;
    left: 0;
    width: 1200px;
    margin: 0;
    text-align: center;
    font-style: normal;
  }
  .legal-info {
    top: 404px;
    font-size: 25px;
    line-height: 30.5px;
    color: var(--legal-text);
  }
  .winery-address {
    top: 566px;
    font-size: 24px;
    line-height: 30px;
    color: var(--address-text);
  }
  .legal-info span,
  .winery-address span {
    display: block;
  }
</style>
</head>
<body>
  <main class="back-label">
    <header class="brand">
      <span class="brand-dot"></span>
      <h1 class="brand-name">Brandauer</h1>
    </header>

    <div class="divider"></div>

    <p class="legal-info">
      <span>Wein aus Deutschland</span>
      <span>L.-Art.Nr: 01-23/4567</span>
      <span>Abfüller: D-RH 123 456</span>
    </p>

    <address class="winery-address">
      <span>Familienweingut</span>
      <span>Brandauer</span>
      <span>Lindenstrasse 7</span>
      <span>weingut-brandauer-beispiel.de</span>
    </address>
  </main>
</body>
</html>
```